Stylish Business Cards Wanted

- DOUBLE SIDED Design Required -

High end, edgy cards for a corporate and personal stylist. Must include logo,
Name: Belinda Harwick
Title: Director and Stylist
telephone : +61 8 7142 5809
email: belinda@theloombriefing.example
website: theloombriefing.example
Tag: Corporate Workwear & Uniform Specialist | Personal Stylist
Would like nice icons for telephone, email, website

Target Market(s)

Businesses wanting stylish uniforms, people wanting stylish wardrobes

Industry/Entity Type

Corporate Workwear Stylist

Contact Information for Business Card

I would like black, white and gold foiling incorporated in the design - possibly a touch of the other colours on my branding guide attached Name: Belinda Harwick Title: Director and Stylist telephone : +61 8 7142 5809 email: belinda@theloombriefing.example website: theloombriefing.example Tag: Corporate Workwear & Uniform Specialist | Personal Stylist Would like nice icons for telephone, email, website

Font styles to use
Other font styles liked:
• Raleway

Colors

Designer to choose colors to be used in the design.

Requirements
Must have
• Gold foil accents

```html
<!DOCTYPE html>
<html lang="en">
<head>
<meta charset="utf-8">
<title>The Loom Briefing – Business Cards</title>
<link href="https://fonts.googleapis.com/css2?family=Raleway:wght@600;700&family=Arimo:wght@400&family=Open+Sans:wght@400&display=swap" rel="stylesheet">
<style>
  :root {
    --backdrop: #7a5640;
    --card-white: #ffffff;
    --ink: #000000;
    --logo-ink: #333333;
    --gold: #e3bd5e;
    --gold-soft: #f6ecd3;
    --text-light: #ffffff;
  }
  * { margin: 0; padding: 0; box-sizing: border-box; }
  html, body { width: 1200px; height: 960px; overflow: hidden; }
  body { background: var(--backdrop); position: relative; font-family: "Arimo", Arial, sans-serif; }

  .card {
    position: absolute;
    width: 602px;
    height: 343px;
    border-radius: 18px;
    overflow: hidden;
    background: var(--card-white);
    box-shadow: 0 2px 6px rgba(0,0,0,0.35);
  }
  .card--front { left: 313px; top: 113px; }
  .card--back { left: 309px; top: 472px; }

  .front-wave { position: absolute; inset: 0; width: 100%; height: 100%; }

  .brand-name {
    font-family: "Raleway", sans-serif;
    font-weight: 700;
    color: var(--logo-ink);
    white-space: nowrap;
  }
  .card--front .brand-name {
    position: absolute;
    left: 160px; top: 121px;
    transform: translate(-50%, -50%);
    font-size: 27px;
  }

  .holder {
    position: absolute;
    right: 36px; top: 120px;
    text-align: right;
  }
  .holder-name {
    font-family: "Raleway", sans-serif;
    font-weight: 700;
    font-size: 12px;
    letter-spacing: 2.6px;
    color: var(--gold);
  }
  .holder-title {
    font-family: "Open Sans", sans-serif;
    font-size: 7.5px;
    color: var(--text-light);
    margin-top: 1px;
  }

  .contact-list { list-style: none; }
  .contact-item {
    position: absolute;
    right: 28px;
    display: flex;
    align-items: center;
    gap: 12px;
    color: var(--text-light);
    font-size: 16px;
    white-space: nowrap;
    transform: translateY(-50%);
  }
  .contact-item svg { width: 20px; height: 20px; flex: none; }
  .contact-item--phone { top: 224px; }
  .contact-item--email { top: 259px; font-size: 14.5px; }
  .contact-item--web { top: 294px; }

  .tagline {
    position: absolute;
    left: 18px; top: 318px;
    transform: translateY(-50%);
    color: var(--text-light);
    font-size: 12.5px;
    white-space: nowrap;
  }

  .back-pattern {
    position: absolute; inset: 0;
    background: linear-gradient(135deg, var(--gold-soft), #fbf5e6 50%, var(--gold-soft));
  }
  .card--back .brand-name {
    position: absolute;
    left: 50%; top: 172px;
    transform: translate(-50%, -50%);
    font-size: 40px;
  }
</style>
</head>
<body>

<section class="card card--front" aria-label="Card front">
  <svg class="front-wave" viewBox="0 0 602 343" preserveAspectRatio="none" aria-hidden="true">
    <path fill="var(--gold)" d="M0,212 C60,246 110,266 150,266 C250,264 320,182 420,104 C480,60 540,46 602,52 L602,343 L0,343 Z"/>
    <path fill="var(--card-white)" d="M0,236 C60,266 110,288 150,287 C250,285 320,200 420,118 C480,70 540,54 602,58 L602,343 L0,343 Z"/>
    <path fill="var(--ink)" d="M0,240 C60,270 110,291 150,290 C250,288 320,203 420,121 C480,73 540,58 602,62 L602,343 L0,343 Z"/>
  </svg>

  <div class="brand-name">The Loom Briefing</div>

  <div class="holder">
    <div class="holder-name">BELINDA HARWICK</div>
    <div class="holder-title">Director and Stylist</div>
  </div>

  <ul class="contact-list">
    <li class="contact-item contact-item--phone">
      <span>+61 8 7142 5809</span>
      <svg viewBox="0 0 24 24" aria-hidden="true"><path fill="var(--gold)" d="M6.6 3.5l2.6 3.2c.4.5.4 1.1 0 1.6L8 9.6c1 2.4 3 4.4 5.4 5.5l1.3-1.2c.5-.4 1.1-.4 1.6 0l3.2 2.6c.5.4.5 1.1.1 1.6l-1.6 1.8c-.6.6-1.5.8-2.3.5C9.8 18.3 5.7 14.2 3.6 8.3c-.3-.8-.1-1.7.5-2.3L5.9 4c.2-.6 1-.6.7-.5z"/></svg>
    </li>
    <li class="contact-item contact-item--email">
      <span>belinda@theloombriefing.example</span>
      <svg viewBox="0 0 24 24" aria-hidden="true"><rect x="2.5" y="6" width="19" height="12.5" fill="var(--gold)"/><path d="M2.5 6l9.5 7 9.5-7M2.5 18.5l7-6M21.5 18.5l-7-6" fill="none" stroke="var(--ink)" stroke-width="1.2"/></svg>
    </li>
    <li class="contact-item contact-item--web">
      <span>theloombriefing.example</span>
      <svg viewBox="0 0 24 24" aria-hidden="true"><g fill="none" stroke="var(--gold)" stroke-width="1.5"><circle cx="12" cy="12" r="9.5"/><ellipse cx="12" cy="12" rx="4.2" ry="9.5"/><line x1="2.5" y1="12" x2="21.5" y2="12"/><path d="M4 7h16M4 17h16"/></g></svg>
    </li>
  </ul>

  <div class="tagline">Corporate Workwear &amp; Uniform Specialist | Personal Stylist</div>
</section>

<section class="card card--back" aria-label="Card back">
  <div class="back-pattern" role="img" aria-label="Faint repeating brand pattern in pale gold across the card"></div>
  <div class="brand-name">The Loom Briefing</div>
</section>

</body>
</html>
```